KORVEN Medical needs bold attention catching website for healthcare professionals(target)

I need a hero page as well as a products and about page for a website of mine. I specialize in orthopedic instruments . Specifically bone drills and saws. This whole company was founded to bring superb quality highly discounted medical instruments. Specifically bone drills, bone saws, k-wires and pins. Two main points should be cost savings and superior quality.

Target Market(s)

healthcare professionals Surgeons and hospital material managers

Number of Pages Required

3 page

Font styles to use
Serif

Colors

Designer to choose colors to be used in the design.

Requirements
Must have
• colors should match logo design

```html
<!DOCTYPE html>
<html lang="en">
<head>
<meta charset="utf-8">
<title>KORVEN Medical</title>
<link href="https://fonts.googleapis.com/css2?family=Lato:wght@400;700;900&display=swap" rel="stylesheet">
<style>
:root{
  --orange:#f07c21;
  --orange-dark:#e56f14;
  --ink:#1b1b1b;
  --text:#3a3a3a;
  --light:#f2f2f2;
  --white:#ffffff;
  --footer:#1e1e1e;
  --footer-text:#d8d8d8;
}
*{margin:0;padding:0;box-sizing:border-box}
html,body{width:1200px;height:4019px;overflow:hidden}
body{font-family:'Lato',sans-serif;color:var(--text);background:var(--white);position:relative}
.abs{position:absolute}
.btn{position:absolute;display:flex;align-items:center;justify-content:center;background:var(--orange);color:var(--white);font-weight:700;font-size:17px;border-radius:24px;text-transform:uppercase}
.btn-dark{background:var(--ink)}
.section-title{position:absolute;left:0;width:1200px;text-align:center;color:var(--ink);font-weight:400;text-transform:uppercase}

/* header */
.site-header{position:absolute;top:0;left:0;width:1200px;height:136px;background:var(--white)}
.brand{position:absolute;left:75px;top:54px;font-size:25px;font-weight:400;color:var(--ink);letter-spacing:.3px;display:flex;align-items:center;gap:9px;white-space:nowrap}
.brand-dot{width:12px;height:12px;border-radius:50%;background:var(--orange);flex:none}
.main-nav a{position:absolute;top:64px;font-size:14px;font-weight:700;color:var(--ink);text-decoration:none;transform:translateX(-50%);white-space:nowrap}
.main-nav a.active{color:var(--orange)}

/* hero */
.hero{position:absolute;top:136px;left:0;width:1200px;height:524px;background:linear-gradient(110deg,#eef1f4 0%,#e3e7ec 45%,#d9dee5 60%,#f2c8a0 72%,#e9ecf0 85%,#f6f7f9 100%)}
.hero h1{position:absolute;left:73px;top:152px;font-size:58px;font-weight:900;color:var(--orange);letter-spacing:.5px;white-space:nowrap}
.hero p{position:absolute;left:75px;top:222px;font-size:30px;font-weight:700;color:var(--ink);line-height:36px;width:480px}
.hero-dots{position:absolute;left:75px;top:476px;display:flex;gap:10px}
.hero-dots span{width:14px;height:14px;border-radius:50%;background:#9a9a9a}
.hero-dots span:first-child{background:var(--orange)}

/* welcome */
.welcome-text{position:absolute;left:75px;top:853px;width:1050px;text-align:center;font-size:16px;line-height:32.5px;color:var(--text)}
.divider{position:absolute;left:75px;top:1139px;width:1052px;height:1px;background:#dcdcdc}

/* products */
.product-card{position:absolute;top:1350px;width:331px;height:487px;background:var(--orange)}
.product-card .photo{height:210px}
.product-card h3{text-align:center;margin-top:36px;font-size:21px;font-weight:900;color:var(--white)}
.product-card p{margin:14px auto 0;width:300px;text-align:center;font-size:14.5px;line-height:27.5px;color:var(--white)}
.product-card .btn{left:90px;top:411px;width:151px;height:44px;font-size:16px}

/* features */
.feature{position:absolute;left:0;width:1200px;background:var(--light)}
.feature h2{position:absolute;font-size:46px;font-weight:400;color:var(--ink);letter-spacing:.5px;white-space:nowrap}
.feature p{position:absolute;width:490px;font-size:15px;line-height:27px;color:var(--text)}

/* clients */
.client{position:absolute;top:2910px;height:50px;display:flex;align-items:center;gap:8px;font-size:26px;font-weight:700;color:var(--ink);white-space:nowrap}
.client i{display:block;width:26px;height:26px;border-radius:50%;background:var(--orange)}

/* reviews */
.reviews{position:absolute;top:3020px;left:0;width:1200px;height:407px;background:var(--light)}

/* subscribe */
.subscribe{position:absolute;top:3427px;left:0;width:1200px;height:295px;background:var(--orange)}
.email-field{position:absolute;left:256px;top:171px;width:473px;height:53px;border-radius:27px;background:var(--white);font-size:16px;color:var(--ink);padding-left:23px;display:flex;align-items:center}

/* footer */
.site-footer{position:absolute;top:3722px;left:0;width:1200px;height:297px;background:var(--footer);color:var(--footer-text)}
.footer-brand{position:absolute;left:75px;top:92px;font-size:25px;color:var(--footer-text);display:flex;align-items:center;gap:9px;white-space:nowrap}
.footer-col{position:absolute;top:48px}
.footer-col h4{font-size:17px;font-weight:700;color:var(--orange);margin-bottom:6px;text-transform:uppercase}
.footer-col li{list-style:none;font-size:13.5px;line-height:27.8px;color:var(--footer-text);white-space:nowrap}
.social{position:absolute;left:75px;top:226px;display:flex;gap:14px;font-size:12px;font-weight:700;color:var(--white)}
</style>
</head>
<body>

<header class="site-header">
  <div class="brand"><span class="brand-dot"></span>KORVEN MEDICAL</div>
  <nav class="main-nav">
    <a class="active" style="left:407px">HOME</a>
    <a style="left:513px">ABOUT US</a>
    <a style="left:638px">PRODUCTS</a>
    <a style="left:758px">SERVICES</a>
    <a style="left:860px">BLOG</a>
    <a style="left:955px">CLIENTS</a>
    <a style="left:1078px">CONTACT US</a>
  </nav>
</header>

<section class="hero" role="img" aria-label="Orthopedic drill bits standing before white and orange geometric shapes">
  <h1>KORVEN MEDICAL</h1>
  <p>Aliquam accumsan facilisis dolor eget interdum...</p>
  <div class="btn" style="left:75px;top:318px;width:186px;height:42px">Read More</div>
  <div class="hero-dots"><span></span><span></span><span></span><span></span></div>
</section>

<h2 class="section-title" style="top:742px;font-size:46px">Welcome to Website</h2>
<p class="welcome-text">Aliquam molestie, mi et imperdiet euismod, dui purus auctor tellus, et interdum lacus lectus et ante. Sed accumsan sollicitudin sapien, sit amet adipiscing turpis gravida ac. In congue, neque ac lobortis volutpat, libero mauris varius mi, vitae suscipit ipsum ligula vitae risus. Quisque magna purus, rutrum quis varius et, venenatis eget tellus. Sed non dui non ligula suscipit condimentum uspendisse vitae dui sit amet enim dapibus euismod et eget risus.</p>
<div class="btn" style="left:524px;top:1022px;width:152px;height:44px">Read More</div>
<div class="divider"></div>

<h2 class="section-title" style="top:1222px;font-size:46px">Our Products</h2>

<article class="product-card" style="left:75px">
  <div class="photo" role="img" aria-label="Surgeon using a bone drill" style="background:linear-gradient(135deg,#3a3530,#8a7a6a 55%,#2c2824)"></div>
  <h3>BONE DRILLS</h3>
  <p>Pellentesque in ligula viverra, mollis est sit amet, egestas turpis. Maecenas ac blandit ipsum. Aliquam erat volutpat. Ut semper porttitor justo a interdum</p>
  <div class="btn btn-dark">Read More</div>
</article>
<article class="product-card" style="left:435px">
  <div class="photo" role="img" aria-label="Bone saws laid out on a white cloth" style="background:linear-gradient(135deg,#6c6c6c,#cfcfcf 50%,#8a8a8a)"></div>
  <h3>BONE SAWS</h3>
  <p>Pellentesque in ligula viverra, mollis est sit amet, egestas turpis. Maecenas ac blandit ipsum. Aliquam erat volutpat. Ut semper porttitor justo a interdum</p>
  <div class="btn btn-dark">Read More</div>
</article>
<article class="product-card" style="left:796px">
  <div class="photo" role="img" aria-label="Gloved hand holding a bundle of K-wires" style="background:linear-gradient(135deg,#8a8f66,#d8d2c0 55%,#9aa0a8)"></div>
  <h3>K-WIRES AND PINS</h3>
  <p>Pellentesque in ligula viverra, mollis est sit amet, egestas turpis. Maecenas ac blandit ipsum. Aliquam erat volutpat. Ut semper porttitor justo a interdum</p>
  <div class="btn btn-dark">Read More</div>
</article>

<section class="feature" style="top:1907px;height:435px">
  <div class="abs" role="img" aria-label="Hand giving a thumbs up beside stacks of coins" style="left:0;top:0;width:600px;height:435px;clip-path:polygon(0 0,549px 0,600px 435px,0 435px);background:linear-gradient(135deg,#6a6a40,#c7bf86 45%,#57502e)"></div>
  <svg class="abs" style="left:634px;top:65px" width="66" height="44" viewBox="0 0 66 44" fill="none" stroke="#f07c21" stroke-width="3">
    <rect x="2" y="2" width="62" height="40" rx="3"/><rect x="9" y="8" width="48" height="28" rx="2"/><circle cx="33" cy="22" r="9"/>
  </svg>
  <h2 style="left:634px;top:130px">COST SAVINGS</h2>
  <p style="left:634px;top:200px">Aliquam molestie, mi et imperdiet euismod, dui purus auctor tellus, et interdum lacus lectus et ante. Sed accumsan sollicitudin sapien, sit amet adipiscing turpis gravida ac. In congue, neque ac lobortis volutpat, libero mauris varius mi, vitae suscipit ipsum ligula vitae risus...</p>
  <div class="btn" style="left:635px;top:327px;width:152px;height:44px">Read More</div>
</section>

<section class="feature" style="top:2342px;height:436px">
  <div class="abs" role="img" aria-label="Close view of a surgical bone saw" style="left:600px;top:0;width:600px;height:436px;clip-path:polygon(1px 0,600px 0,600px 436px,52px 436px);background:linear-gradient(135deg,#9a9a9a,#e4e4e4 45%,#5e5e5e 75%,#cfcfcf)"></div>
  <svg class="abs" style="left:73px;top:60px" width="56" height="54" viewBox="0 0 56 54" fill="none" stroke="#f07c21" stroke-width="3" stroke-linejoin="round">
    <rect x="2" y="24" width="12" height="27"/><path d="M14 26 L24 12 L26 3 Q33 3 32 14 L30 22 L48 22 Q54 23 52 30 L48 47 Q46 51 40 51 L14 51"/>
  </svg>
  <h2 style="left:73px;top:124px">SUPERIOR QUALITY</h2>
  <p style="left:75px;top:190px">Aliquam molestie, mi et imperdiet euismod, dui purus auctor tellus, et interdum lacus lectus et ante. Sed accumsan sollicitudin sapien, sit amet adipiscing turpis gravida ac. In congue, neque ac lobortis volutpat, libero mauris varius mi, vitae suscipit ipsum ligula vitae risus...</p>
  <div class="btn" style="left:75px;top:322px;width:152px;height:44px">Read More</div>
</section>

<h2 class="section-title" style="top:2834px;font-size:28px">Our Clients</h2>
<div class="client" style="left:175px"><i></i>Arbormark</div>
<div class="client" style="left:402px"><i></i>Brightwell</div>
<div class="client" style="left:642px"><i></i>Corvane</div>
<div class="client" style="left:860px"><i></i>Tandry</div>

<section class="reviews">
  <h2 class="section-title" style="top:55px;font-size:46px">Reviews</h2>
  <p class="abs" style="left:0;top:143px;width:1200px;text-align:center;font-size:17px;color:var(--orange)">"ALIQUAM MAXIMUS NEC TORTOR UT PORTA....."</p>
  <p class="abs" style="left:70px;top:181px;width:1060px;text-align:center;font-size:18.5px;line-height:28px;color:var(--text)">Quisque iaculis ultricies tortor, non eleifend enim rhoncus eu. Vestibulum ante ipsum primis in faucibus orci luctus et ultrices posuere cubilia Curae; Ut eu posuere velit, in ornare dolor. Curabitur varius, lectus quis viverra fermentum, turpis risus ultricies urna, a pretium lorem massa a ante.</p>
  <p class="abs" style="left:0;top:278px;width:1200px;text-align:center;font-size:14px;color:var(--orange)">-NAME HEADING</p>
  <div class="abs" style="left:564px;top:340px;display:flex;gap:11px">
    <span style="width:10px;height:10px;border-radius:50%;background:var(--ink)"></span>
    <span style="width:10px;height:10px;border-radius:50%;background:#9a9a9a"></span>
    <span style="width:10px;height:10px;border-radius:50%;background:#9a9a9a"></span>
    <span style="width:10px;height:10px;border-radius:50%;background:#9a9a9a"></span>
  </div>
</section>

<section class="subscribe">
  <h2 class="section-title" style="top:60px;font-size:48px;color:var(--white);letter-spacing:1.5px">Email&nbsp; Subscribe</h2>
  <p class="abs" style="left:0;top:129px;width:1200px;text-align:center;font-size:16px;color:var(--white)">Nullam id nulla rhoncus, tincidunt quam eget, imperdiet orci.</p>
  <div class="email-field">Enter Email Address</div>
  <div class="btn btn-dark" style="left:741px;top:171px;width:203px;height:53px;border-radius:27px;font-size:16px">Subscribe</div>
</section>

<footer class="site-footer">
  <div class="footer-brand"><span class="brand-dot"></span>KORVEN MEDICAL</div>
  <p class="abs" style="left:75px;top:172px;font-size:12.5px;line-height:22px">Copyright © 2019 Company Name.<br>All Right Reserved</p>
  <div class="social"><span>Feed</span><span>Notes</span><span>Video</span><span>Group</span><span>Photos</span><span>Work</span></div>
  <div class="footer-col" style="left:379px"><h4>Sitemap</h4><ul><li>Home</li><li>About Us</li><li>Products</li><li>Services</li><li>Blog</li><li>Clients</li><li>Contact Us</li></ul></div>
  <div class="footer-col" style="left:620px"><h4>Resources</h4><ul><li>Fusce scelerisque</li><li>Velit id dui</li><li>Fermentum efficitur</li><li>Sed et congue dolor</li><li>Fusce gravida</li><li>Vestibulum</li></ul></div>
  <div class="footer-col" style="left:885px"><h4>Contact Info</h4>
    <ul>
      <li style="font-weight:700;color:var(--white);font-size:15px">Company Name</li>
      <li style="line-height:23px;margin-top:2px">4120 Harbor Ridge Dr, Suite 210<br>Duluth, MN 55802<br>USA</li>
      <li style="margin-top:8px;display:flex;align-items:center;gap:18px"><svg width="14" height="14" viewBox="0 0 24 24" fill="#ffffff"><path d="M6.6 10.8c1.4 2.8 3.8 5.1 6.6 6.6l2.2-2.2c.3-.3.7-.4 1-.2 1.1.4 2.3.6 3.6.6.6 0 1 .4 1 1V20c0 .6-.4 1-1 1C10.6 21 3 13.4 3 4c0-.6.4-1 1-1h3.5c.6 0 1 .4 1 1 0 1.3.2 2.5.6 3.6.1.3 0 .7-.2 1z"/></svg>1-800-555-0142</li>
      <li style="display:flex;align-items:center;gap:18px"><svg width="14" height="11" viewBox="0 0 24 18" fill="#ffffff"><path d="M0 0h24v2L12 9 0 2zM0 4l12 7 12-7v14H0z"/></svg>hello@korvenmedical.com</li>
    </ul>
  </div>
</footer>

</body>
</html>
```